Clean business card with logo provided

I want a card that will stand out among the masses. I need the color and image to show professionalism and yet have a family appeal showing that I only deal with win/win scenarios. The back of the card will be used to take notes about the individual so I can use that in my database entry. I like modern design but need professionalism in it also. It needs to fit my "clean, safe, and affordable housing" motto. I need to be able to write on the file and update the card details for my employees.

Target Market(s)

Investors looking to make investment income through real estate

Industry/Entity Type

Real Estate

Contact Information for Business Card

Brent Kovalich
blank address, city, st, zip code
480-555-3174
brentkovalich@ridgeworthrentals.example
www.ridgeworthrentals.example

Font styles to use
Sans Serif

Requirements
Must have
• I would like the back of the card to have lines for info. example
• Met/Visited: Date:
• Interets:
Nice to have
• I want the cards color to match the logo background color. Font with details to be san serif and black. I want the card rectangular with square corners. Standard business card size. I would like to see cards designed with both images to see which i prefer more.

```html
<!DOCTYPE html>
<html lang="en">
<head>
<meta charset="utf-8">
<title>Ridgeworth Rentals LLC — Business Card</title>
<link href="https://fonts.googleapis.com/css2?family=Cinzel:wght@400&family=Open+Sans:wght@400&display=swap" rel="stylesheet">
<style>
  :root {
    --backdrop: #9c9c9c;
    --teal: #17a3b8;
    --ink: #050505;
    --paper: #f1f1f1;
    --white: #ffffff;
    --rule: #1c1c1c;
    --tagline: #d9f3f7;
  }
  * { margin: 0; padding: 0; box-sizing: border-box; }
  html, body {
    width: 1105px;
    height: 1200px;
    overflow: hidden;
    background: var(--backdrop);
    font-family: "Open Sans", Arial, sans-serif;
  }
  .card {
    position: absolute;
    left: 180px;
    width: 746px;
    height: 428px;
    overflow: hidden;
  }
  .card--front { top: 117px; background: var(--ink); }
  .card--back { top: 637px; background: var(--paper); }

  /* Front */
  .front-art {
    position: absolute;
    left: 0; top: 0;
    width: 300px; height: 428px;
    background: linear-gradient(100deg, #000 0%, #1a1a1a 45%, #cfcfcf 75%, #000 100%);
  }
  .front-panel {
    position: absolute;
    left: 0; top: 0;
    width: 746px; height: 428px;
  }
  .brand {
    position: absolute;
    font-family: "Cinzel", "Times New Roman", serif;
    font-weight: 400;
    letter-spacing: 2px;
    white-space: nowrap;
  }
  .brand--front {
    right: 30px; top: 34px;
    font-size: 26px;
    color: var(--white);
  }
  .tagline {
    position: absolute;
    font-size: 12px;
    white-space: nowrap;
  }
  .tagline--front { left: 352px; top: 80px; color: var(--tagline); }
  .holder-name {
    position: absolute;
    right: 50px; top: 147px;
    font-family: "Cinzel", "Times New Roman", serif;
    font-size: 27px;
    color: var(--white);
    letter-spacing: 1px;
  }
  .address {
    position: absolute;
    right: 48px; top: 248px;
    text-align: right;
    color: var(--white);
    font-size: 20px;
    line-height: 27px;
  }
  .contact-list {
    position: absolute;
    right: 48px; top: 308px;
    list-style: none;
    color: var(--white);
    font-size: 18px;
    line-height: 28px;
    text-align: right;
  }
  .contact-list li { display: flex; justify-content: flex-end; align-items: center; gap: 10px; }
  .contact-list svg { width: 16px; height: 16px; fill: var(--white); flex: none; }

  /* Back */
  .back-band {
    position: absolute;
    left: 0; top: 0;
    width: 746px; height: 180px;
    background: var(--ink);
  }
  .brand--back {
    left: 0; right: 0; top: 58px;
    text-align: center;
    font-size: 32px;
    color: var(--teal);
  }
  .tagline--back { left: 0; right: 0; top: 128px; text-align: center; color: var(--teal); }
  .note-field {
    position: absolute;
    left: 57px;
    width: 622px;
    display: flex;
    align-items: flex-end;
    color: var(--teal);
    font-size: 19px;
    line-height: 1;
  }
  .note-field .line { flex: 1; border-bottom: 1.5px solid var(--rule); margin-left: 4px; margin-bottom: 2px; }
  .note-field--met { top: 214px; }
  .note-field--date { top: 265px; }
  .note-field--interests { top: 316px; }
  .note-field--extra { top: 366px; }
</style>
</head>
<body>

<section class="card card--front">
  <div class="front-art" role="img" aria-label="Large manta ray illustration in white and black"></div>
  <svg class="front-panel" viewBox="0 0 746 428" aria-hidden="true">
    <path d="M274,0 H746 V428 H286 C270,330 266,120 274,0 Z" fill="var(--teal)"/>
  </svg>
  <div class="brand brand--front">RIDGEWORTH RENTALS LLC</div>
  <p class="tagline tagline--front">Providing clean, safe, and affordable housing</p>
  <h1 class="holder-name">BRENT KOVALICH</h1>
  <p class="address">4120 Alder Crest Road<br>Juneau, Alaska 99801</p>
  <ul class="contact-list">
    <li>480-555-3174
      <svg viewBox="0 0 24 24"><path d="M6.6 10.8a15.1 15.1 0 0 0 6.6 6.6l2.2-2.2a1 1 0 0 1 1-.25 11.4 11.4 0 0 0 3.6.57 1 1 0 0 1 1 1V20a1 1 0 0 1-1 1A17 17 0 0 1 3 4a1 1 0 0 1 1-1h3.5a1 1 0 0 1 1 1c0 1.25.2 2.45.57 3.57a1 1 0 0 1-.25 1z"/></svg>
    </li>
    <li>brentkovalich@ridgeworthrentals.example
      <svg viewBox="0 0 24 24"><path d="M2 5h20v14H2z M3.5 6.5 12 13l8.5-6.5" fill="none" stroke="#fff" stroke-width="2"/></svg>
    </li>
    <li>www.ridgeworthrentals.example
      <svg viewBox="0 0 24 24"><circle cx="12" cy="12" r="10"/><path d="M2 12h20M12 2c3 3 3 17 0 20M12 2c-3 3-3 17 0 20" fill="none" stroke="var(--teal)" stroke-width="1.5"/></svg>
    </li>
  </ul>
</section>

<section class="card card--back">
  <div class="back-band"></div>
  <div class="brand brand--back">RIDGEWORTH RENTALS LLC</div>
  <p class="tagline tagline--back">Providing clean, safe, and affordable housing</p>
  <div class="note-field note-field--met"><span>MET/VISITED:</span><span class="line"></span></div>
  <div class="note-field note-field--date"><span>DATE:</span><span class="line"></span></div>
  <div class="note-field note-field--interests"><span>INTERESTS:</span><span class="line"></span></div>
  <div class="note-field note-field--extra"><span class="line"></span></div>
</section>

</body>
</html>
```